New, modern business card for growing audiology practice

We need a new business card for our audiology practice. Our logo and website have recently changed (more modern) and we want our business cards to reflect this change.
We conduct hearing tests, perform earwax removals, and fit & dispense hearing aids to our patients. We are a family owned practice in which the owner is the one who works directly with the patient. I have attached logos in various formats to use, as well as two ideas I found on this website; as well as a scanned copy of our current logo. Good luck!

Industry/Entity Type

Business

Contact Information for Business Card

Company name: Tolvera Hearing Center
Provider name: Peter Wolstenby, Au.D. F/NSB
Phone number: (440) 683-5127
Address: 837 W. Lindell Ave. Maple Ridge, OH 44198
email: tolverahearing@postvane.com
website: tolverahearing.com

Colors
000000
aaaaaa
dbdbdb
cacaca
9bcb3c
afd23c
cadf82
b1b1b1

Requirements
Must have
• My card must include information in the "details" section. In the attached images, I found a few that I liked and I would like to model after - "brisky bouncin'" and "Sound Method Center".
• Must be horizontal.
• Must include logos provided. I uploaded them in various file formats and various ways.
• Must match logo font, if possible, if not, please get as close as you can.
Nice to have
• I really like the idea of having a color on one side with just the logo and company name and the contact information and provider name on the other side. I also really like the idea of having the main color dominating on the logo/company side with accent of that same color on the contact side of the card.
Should not have
• Must not be vertical.

```html
<!DOCTYPE html>
<html lang="en">
<head>
<meta charset="utf-8">
<title>Tolvera Hearing Center – Business Card</title>
<link rel="stylesheet" href="https://fonts.googleapis.com/css2?family=Roboto+Condensed:wght@700&family=Roboto:wght@400;500&family=Lato:wght@400&display=swap">
<style>
  :root {
    --backdrop: #6e4a30;
    --brand-green: #70a035;
    --card-white: #f3f3f3;
    --ink-black: #000000;
    --text-white: #ffffff;
    --logo-ink: #111111;
  }
  * { margin: 0; padding: 0; box-sizing: border-box; }
  html, body { width: 1200px; height: 960px; overflow: hidden; }
  body { background: var(--backdrop); position: relative; }

  .card {
    position: absolute;
    width: 600px;
    height: 343px;
    overflow: hidden;
    box-shadow: 0 2px 6px rgba(0,0,0,.35);
  }
  .card-front { left: 314px; top: 113px; background: var(--brand-green); }
  .card-back { left: 311px; top: 472px; background: var(--ink-black); }

  .front-swoosh { position: absolute; inset: 0; }

  .contact-block {
    position: absolute;
    left: 22px;
    top: 90px;
    color: var(--text-white);
    font-family: "Roboto", Arial, sans-serif;
  }
  .provider-name {
    font-family: "Roboto Condensed", "Arial Narrow", sans-serif;
    font-weight: 700;
    font-size: 21px;
    line-height: 24px;
    letter-spacing: .2px;
  }
  .provider-credentials {
    font-family: "Roboto", Arial, sans-serif;
    font-weight: 500;
    font-size: 14px;
    margin-top: 2px;
  }
  .address { font-size: 14px; line-height: 18px; margin-top: 16px; }
  .contact-lines { list-style: none; margin-top: 10px; font-size: 14px; line-height: 19.5px; }
  .contact-lines li { display: flex; align-items: center; gap: 9px; }
  .contact-lines svg { width: 13px; height: 13px; flex: none; fill: var(--text-white); }

  .brand-lockup {
    position: absolute;
    display: flex;
    align-items: center;
    font-family: "Lato", "Gill Sans", sans-serif;
    font-weight: 400;
    text-transform: uppercase;
    white-space: nowrap;
  }
  .brand-dot { border-radius: 50%; background: var(--brand-green); flex: none; }
  .brand-lockup-front { left: 303px; top: 161px; font-size: 17px; color: var(--logo-ink); gap: 8px; }
  .brand-lockup-front .brand-dot { width: 14px; height: 14px; }
  .brand-lockup-back {
    left: 0; right: 0; top: 152px; justify-content: center;
    font-size: 29px; color: var(--text-white); gap: 14px;
  }
  .brand-lockup-back .brand-dot { width: 22px; height: 22px; }

  .back-website {
    position: absolute;
    left: 0; right: 0; top: 287px;
    text-align: center;
    font-family: "Roboto", Arial, sans-serif;
    font-size: 13px;
    letter-spacing: 5.2px;
    color: var(--text-white);
  }
  .back-website .accent { color: var(--brand-green); }
</style>
</head>
<body>

<section class="card card-front">
  <svg class="front-swoosh" viewBox="0 0 600 343" aria-hidden="true">
    <path d="M320 0 C 225 70, 215 270, 322 343 L 360 343 C 240 270, 240 70, 345 0 Z" fill="var(--ink-black)"/>
    <path d="M322 0 C 230 70, 220 270, 322 343" fill="none" stroke="var(--text-white)" stroke-width="1.2"/>
    <path d="M350 0 C 250 70, 250 270, 355 343 L 600 343 L 600 0 Z" fill="var(--card-white)"/>
    <path d="M337 0 C 243 75, 245 270, 336 330 C 260 265, 258 80, 350 0 Z" fill="var(--brand-green)"/>
  </svg>

  <div class="contact-block">
    <p class="provider-name">PETER WOLSTENBY</p>
    <p class="provider-credentials">AU.D. F/NSB</p>
    <p class="address">837 W. Lindell Ave.<br>Maple Ridge, OH 44198</p>
    <ul class="contact-lines">
      <li>
        <svg viewBox="0 0 16 16" aria-hidden="true"><path d="M3.5 1 L6 1 L7 4.5 L5.3 5.8 C6.2 7.8 8.2 9.8 10.2 10.7 L11.5 9 L15 10 L15 12.5 C15 13.9 13.9 15 12.5 15 C6.7 15 1 9.3 1 3.5 C1 2.1 2.1 1 3.5 1 Z"/></svg>
        (440) 683-5127
      </li>
      <li>
        <svg viewBox="0 0 16 16" aria-hidden="true"><path d="M1 3 H15 V4 L8 8.5 L1 4 Z M1 5.5 L8 10 L15 5.5 V13 H1 Z"/></svg>
        tolverahearing@postvane.com
      </li>
      <li>
        <svg viewBox="0 0 16 16" aria-hidden="true"><circle cx="8" cy="8" r="7"/><path d="M5 4 C7 5 6 7 8 7.5 C9.5 8 8 10 9 12 M10 3 C11 4.5 12.5 4 13 6" fill="none" stroke="var(--brand-green)" stroke-width="1.4"/></svg>
        tolverahearing.com
      </li>
    </ul>
  </div>

  <div class="brand-lockup brand-lockup-front">
    <span class="brand-dot"></span>
    <span class="brand-name">Tolvera Hearing Center</span>
  </div>
</section>

<section class="card card-back">
  <div class="brand-lockup brand-lockup-back">
    <span class="brand-dot"></span>
    <span class="brand-name">Tolvera Hearing Center</span>
  </div>
  <p class="back-website">www.<span class="accent">tolverahearing</span>.com</p>
</section>

</body>
</html>
```